Local Chiropractoc needs Modern Website

This website needs to have an upscale look with a very modern feel.

This is for a home page psd layout and an interior page psd file so 2 files total

Below is the information and websites to reference

Add Logo that is attached.

Build a color scheme similar to this website image titled "chiro-1" using the golds, whites, blacks and browns from the color of the logo

I want to see a light background so it makes the images and logo stick out

Must Include these pages in a horizontal menu bar in this order:
Home, Why Fair Ridge?, How Chiropractic Helps, Ask the Doctor, Work Place Wellness, Request an Appointment, Blog, Contact Us

Please add the following social media logos to the top and footer of the website: Chatterly, Plexo+, Vidzio

Build a "classy looking" Make An Appointment Button into the header with the contact info below

Phone Number:
555-014-2297

Address:
4172 North Maple Blvd, Suite #7
Brookhaven, OR 97520

This website needs 4 rotating banners. Please reference a layout similar to this for the banners: http://hollowpinespine.com/. However design it nicer than this website

Below are the description for each banner

Rotating Banner #1
Use Image: Patients are Saying
Add a line of text: "What our Patients are Saying"

Rotating Banner #2
Use Image: Becoming a Patient
Add a line of text: "Interested in Becoming a Patient"

Rotating Banner #3
Use Image: Dinner with Doctor
Add a line of text: "Win A free Dinner with Dr. Hollins"

Rotating Banner #4
Use Image: Chatterly
Add a line of text: Follow us on Chatterly
Bullet point these 4 lines underneath the "Follow us on Chatterly" text:
- Cutting Edge Health News
- Healthy Recipes
- Newest Health Products
- Clinic Events

I'd like to see a free consultation box similar to the "chiro-1" image. Fields to include are: First Name, Last Name, Phone Number, Comments

For the body, please fill it with latin text. Please design a professional 2 column layout similar to the www.hollowpinespine.com website. (DO NOT COPY THIS WEBSITE, USE IT AS REFERENCE)

In the left column include in this order:
Video
Rate us on Plexo Button, Find us on Chatterly Button
Welcome Letter

In the right column include this:

Office Hours
Monday: 8:00-11:00, 2:00-5:00
Tuesday: 8:30-11:00, 2:00-5:30
Wednesday: 8:00-11:00, 2:00-5:00
Thursday: 10:00-12:00, 2:30-5:00
Friday: 8:00-10:00, 1:00-5:00
Saturday: Closed
Sunday: Closed

Patient Testimonials
Fill with a latin text testimonial. This spot will rotate different testimonials

For the footer please design something similar to the layout of this: http://www.tidewellhealer.com/

Also include in the Footer: Powered by Crestline Pixel Group

```html
<!DOCTYPE html>
<html lang="en">
<head>
<meta charset="utf-8">
<title>Fair Ridge Chiropractic</title>
<link href="https://fonts.googleapis.com/css2?family=Open+Sans:ital,wght@0,400;0,600;0,700;1,400&family=Titillium+Web:wght@600;700&display=swap" rel="stylesheet">
<style>
:root{
  --gold:#b8975a;
  --gold-dark:#a6864b;
  --ink:#2b2b2b;
  --ink-soft:#3a3a3a;
  --page:#f1f1f1;
  --paper:#ffffff;
  --text:#6f6f6f;
  --rule:#e6e6e6;
  --row:#f3f3f3;
}
*{margin:0;padding:0;box-sizing:border-box}
html,body{width:805px;height:1200px;overflow:hidden}
body{background:var(--page);font-family:"Open Sans",sans-serif;color:var(--text);position:relative}
.abs{position:absolute}
h2,h3,.display{font-family:"Titillium Web",sans-serif}

/* header */
.brand{left:107px;top:38px;display:flex;align-items:center;gap:8px}
.brand-mark{width:14px;height:60px;background:var(--ink)}
.brand-name{font-family:"Titillium Web",sans-serif;font-weight:700;color:var(--ink);font-size:27px;line-height:26px;letter-spacing:.5px}
.brand-name small{display:block;font-size:13px;letter-spacing:2px;line-height:16px}
.social{display:flex;gap:3px}
.social-top{left:653px;top:50px}
.social span{width:18px;height:18px;border:1px solid var(--gold);border-radius:50%;display:flex;align-items:center;justify-content:center;font-size:8px;font-weight:700;color:var(--gold)}
.social span.on{background:var(--gold);color:#fff}
.contact-bar{left:347px;top:79px;width:254px;height:30px;background:var(--ink);display:flex;color:#fff;font-size:7px;line-height:9px}
.contact-item{display:flex;align-items:center;gap:8px;padding:0 8px}
.contact-item + .contact-item{border-left:1px solid #444}
.contact-item b{font-weight:700}
.contact-item i{color:#9a9a9a;font-style:italic}
.appt{left:597px;top:79px;width:115px;height:30px;background:var(--gold);color:#fff;font-size:7px;font-weight:700;letter-spacing:.3px;display:flex;align-items:center;justify-content:center;clip-path:polygon(6% 0,100% 0,100% 100%,0 100%,6% 50%,0 0)}

/* navigation */
.nav{left:93px;top:121px;width:619px;height:40px;background:var(--ink);display:flex;font-size:6.5px;color:#fff;text-transform:uppercase}
.nav a{display:flex;align-items:center;justify-content:center;color:inherit;text-decoration:none;border-right:1px solid #3d3d3d}
.nav a:last-child{border-right:0}
.nav a.active{background:var(--gold)}

/* hero */
.hero{left:93px;top:171px;width:619px;height:202px}
.hero-copy{left:453px;top:36px;width:150px;color:#fff}
.hero-copy h2{font-size:15px;line-height:18px;font-weight:600}
.hero-copy p{font-size:6.5px;line-height:13px;margin-top:9px}
.btn-light{display:inline-block;margin-top:12px;background:#fff;color:var(--ink);font-size:6.5px;padding:6px 10px;border-radius:2px}
.dots{display:flex;gap:3px}
.dots span{width:5px;height:5px;border-radius:50%;background:rgba(255,255,255,.45)}
.dots span.on{background:#fff}

/* content */
.sheet{left:93px;top:382px;width:619px;height:718px;background:var(--paper);border:1px solid #e8e8e8}
.section-title{font-size:8.5px;font-weight:700;color:var(--ink);display:flex;align-items:center;gap:6px;text-transform:uppercase}
.section-title::before{content:"";width:2px;height:8px;background:var(--gold)}
.section-title::after{content:"";flex:1;height:6px;background:#f5f5f5}
.video{left:108px;top:435px;width:388px;height:201px;border:1px solid var(--rule);padding:5px}
.video-frame{width:100%;height:169px;background:linear-gradient(180deg,#c9cfd0,#a6ad8a 70%,#8b9462)}
.video-bar{height:20px;background:var(--ink);display:flex;align-items:center;gap:6px;padding:0 6px;font-size:5.5px;color:#888}
.video-track{flex:1;height:2px;background:#555;position:relative}
.video-track::before{content:"";position:absolute;left:0;top:0;width:30%;height:2px;background:var(--gold)}
.video-track::after{content:"";position:absolute;left:30%;top:-2px;width:6px;height:6px;border-radius:50%;background:#fff}
.play{left:183px;top:85px;width:22px;height:20px;background:rgba(255,255,255,.55);display:flex;align-items:center;justify-content:center}
.body-text{font-size:6.6px;line-height:15.2px;color:var(--text)}
.letter-photo{left:309px;top:677px;width:187px;height:164px;background:linear-gradient(160deg,#9fb784,#d8c8b4 60%,#c49aa8)}

/* sidebar */
.consult{left:510px;top:413px;width:187px;height:231px}
.consult-copy{left:0;top:9px;width:187px;text-align:center;color:#fff}
.consult-copy p{font-size:7px}
.consult-copy h3{font-size:11px;line-height:13px;font-weight:700}
.consult-copy em{display:block;margin-top:20px;font-size:7px;font-weight:600}
.field{left:10px;width:166px;height:17px;background:#fff;border-radius:2px;font-size:5.5px;color:#555;padding:5px 10px}
.field.gold{color:var(--gold)}
.submit{left:10px;top:184px;width:52px;height:18px;background:var(--gold);color:#fff;font-size:6px;font-weight:600;display:flex;align-items:center;justify-content:center;border-radius:2px}
.badge-btn{left:510px;width:187px;height:30px;display:flex;background:var(--ink);border-right:2px solid var(--gold)}
.badge-btn .ico{width:31px;background:var(--gold);color:#fff;font-weight:700;font-size:12px;display:flex;align-items:center;justify-content:center}
.badge-btn .lbl{flex:1;text-align:center;color:#fff;font-size:5.5px;line-height:7px;padding-top:4px}
.badge-btn .lbl b{display:block;font-family:"Titillium Web",sans-serif;color:var(--gold);font-size:14px;line-height:16px;letter-spacing:.5px}
.hours{left:510px;top:739px;width:187px;border:1px solid var(--rule)}
.hours h3{background:var(--gold);color:#fff;text-align:center;font-size:9px;height:24px;line-height:24px}
.hours-row{display:flex;justify-content:space-between;padding:0 9px;height:18.3px;align-items:center;font-size:5.5px}
.hours-row:nth-child(even){background:var(--row)}
.hours-row span:first-child{font-weight:600;color:var(--ink)}
.hours-row.closed span{color:var(--gold)}
.quote{left:510px;top:932px;width:187px;height:138px;background:#f2f2f2}
.quote-mark{left:20px;top:14px;font-family:Georgia,serif;font-size:38px;line-height:30px;color:var(--gold)}
.quote-text{left:18px;top:14px;width:160px;font-size:6.4px;line-height:13px;font-style:italic;color:#8a8a8a;text-align:justify;text-indent:29px}
.quote-foot{left:0;bottom:0;width:187px;height:20px;background:var(--gold);display:flex;align-items:center;justify-content:space-between;padding:0 16px;color:#fff;font-size:5.8px;font-weight:700}

/* footer */
.foot-links{left:0;top:1099px;width:805px;height:51px;background:var(--gold)}
.foot-nav{left:108px;top:20px;font-size:6.6px;color:#fff;font-weight:600;white-space:nowrap}
.foot-nav span{margin:0 4px}
.foot-brand{left:636px;top:12px;font-family:"Titillium Web",sans-serif;font-weight:700;color:#fff;font-size:12px;line-height:12px;display:flex;gap:5px;align-items:center}
.foot-brand i{width:6px;height:26px;background:#fff}
.foot-brand small{display:block;font-size:6px;letter-spacing:1px;line-height:9px}
.foot-base{left:0;top:1150px;width:805px;height:50px;background:var(--ink);color:#fff;font-size:6.3px;line-height:9px}
.foot-base .social span{width:20px;height:20px;border-radius:2px}
</style>
</head>
<body>

<header>
  <div class="abs brand">
    <span class="brand-mark"></span>
    <div class="brand-name">FAIR RIDGE<small>CHIROPRACTIC</small></div>
  </div>
  <div class="abs social social-top" aria-label="Social links">
    <span>C</span><span class="on">P</span><span>V</span>
  </div>
  <div class="abs contact-bar">
    <div class="contact-item">
      <svg width="12" height="12" viewBox="0 0 24 24"><path fill="#b8975a" d="M6.6 10.8a15 15 0 006.6 6.6l2.2-2.2a1 1 0 011-.25 11.4 11.4 0 003.6.57 1 1 0 011 1V20a1 1 0 01-1 1A17 17 0 013 4a1 1 0 011-1h3.5a1 1 0 011 1c0 1.25.2 2.450.57 3.57a1 1 0 01-.25 1z"/></svg>
      <div><b>555-014-2297</b><br><i>info@example.com</i></div>
    </div>
    <div class="contact-item">
      <svg width="13" height="12" viewBox="0 0 24 22"><path fill="#b8975a" d="M12 1L1 11h3v10h6v-6h4v6h6V11h3z"/></svg>
      <div><b>4172 North Maple Blvd, Suite #7</b><br><i>Brookhaven, OR 97520</i></div>
    </div>
  </div>
  <div class="abs appt">MAKE AN APPOINTMENT</div>

  <nav class="abs nav">
    <a style="width:50px">Home</a>
    <a class="active" style="width:71px">Why Fair Ridge?</a>
    <a style="width:107px">How Chiropractic Helps</a>
    <a style="width:76px">Ask the Doctor</a>
    <a style="width:97px">Work Place Wellness</a>
    <a style="width:109px">Request an Appointment</a>
    <a style="width:40px">Blog</a>
    <a style="width:69px">Contact Us</a>
  </nav>
</header>

<section class="abs hero">
  <svg width="619" height="202" viewBox="0 0 619 202" style="display:block">
    <defs>
      <linearGradient id="heroPhoto" x1="0" x2="1" y1="0" y2="1">
        <stop offset="0" stop-color="#c9a78a"/><stop offset=".5" stop-color="#d9b79a"/><stop offset="1" stop-color="#8f6d52"/>
      </linearGradient>
    </defs>
    <rect width="619" height="202" fill="url(#heroPhoto)" role="img" aria-label="Photo of a smiling family of four"/>
    <path d="M432 0 C395 45 420 120 398 202 L619 202 L619 0 Z" fill="#b8975a"/>
    <path d="M432 0 C395 45 420 120 398 202" fill="none" stroke="#fff" stroke-width="3"/>
  </svg>
  <div class="abs hero-copy">
    <h2>What Our Patients<br>Are Saying?</h2>
    <p>Proin sit amet venenatis ante. Nulla lorem felis, maximus tincidunt felis nec, mattis con dimentum enim. Maecenas non sodales nund.</p>
    <span class="btn-light">Read More</span>
  </div>
  <div class="abs dots" style="left:453px;top:186px"><span></span><span class="on"></span><span></span><span></span></div>
</section>

<main class="abs sheet"></main>

<h2 class="abs section-title" style="left:108px;top:412px;width:388px">Our Videos</h2>
<div class="abs video">
  <div class="video-frame" role="img" aria-label="Video still of a multi-generation family outdoors"></div>
  <div class="video-bar">
    <svg width="6" height="7" viewBox="0 0 6 7"><path d="M0 0L6 3.5 0 7z" fill="#888"/></svg>
    <span>00:28</span><div class="video-track"></div><span>02:36</span>
    <svg width="8" height="7" viewBox="0 0 8 7"><path d="M0 2h2l3-2v7L2 5H0z" fill="#888"/></svg>
  </div>
  <div class="abs play"><svg width="7" height="8" viewBox="0 0 7 8"><path d="M0 0L7 4 0 8z" fill="#fff"/></svg></div>
</div>

<h2 class="abs section-title" style="left:108px;top:655px;width:388px">Welcome Letter</h2>
<div class="abs body-text" style="left:108px;top:674px;width:190px">
  Hello Dear Visitor,<br>
  Vestibulum malesuada tortor volutpat risus finibus, in con sequat nibh dictum. Pellen tesque vestibulum nisi nisl, vel accumsan dui consequat sed. Integer non justo et mi interd um pretium. Proin ut pulvinar eros. Pellentesque at luctus odio, a ullamcorper urna. Nam semper feugiat massa non pulvinar. Curabitur sagittis, odio eget posuere ultricies, sem nisi pulvinar turpis, at laoreet arcu neque lacinia odio. Nulla nec nunc ac felis auctor fermentum quis ut justo. Donec ultricies feugiat accumsan. Integer leo justo, dapi bus id mauris quis, vestibulum rutrum arcu.
</div>
<div class="abs letter-photo" role="img" aria-label="Photo of a laughing family embracing outdoors"></div>
<p class="abs body-text" style="left:108px;top:857px;width:388px;text-align:justify">Vestibulum malesuada tortor volutpat risus finibus, in con sequat nibh dictum. Pellen tesque vestibulum nisi nisl, vel accumsan dui consequat sed. Integer non justo et mi interd um pretium. Proin ut pulvinar eros. Pellentesque at luctus odio, a ullamcorper urna. Nam semper feugiat massa non pulvinar. Curabitur sagittis, odio eget posuere ultricies, sem nisi pulvi nar turpis, at laoreet arcu neque lacinia odio. Nulla nec nunc ac felis auctor fermentum quis ut justo. Donec ultricies feugiat accumsan. Integer leo justo, dapi bus id mauris quis, vestibulum rutrum arcu. Donec diam magna, mattis ac odio id, dignis sim euismod eros. Proin id luctus dolor, vel imperdiet ante. Morbi rhoncus fringilla neque, non tristique ante interdum ac. Etiam lacinia neque sagittis, commodo diam at, ullamcorper urna.</p>
<p class="abs body-text" style="left:108px;top:977px;width:388px;text-align:justify">In sodales velit nec magna pellentesque, nec dignissim eros porta. Nam congue maximus elit. Quisque sapien nunc, lobortis et nulla eu, eleifend sodales velit. Aliquam aliquam eros lectus, facilisis dictum libero feugiat nec. Nunc quis elit pulvinar, aliquam ipsum in, lacinia enim. Fusce a consequat erat. Aliquam urna dui, malesuada in vehicula cursus, porttitor quis risus. Pellentesque tristique consectetur libero, et suscipit eros fringilla et. Morbi fringilla sapien sed elit lobortis, non cursus velit tincidunt.</p>

<aside>
  <div class="abs consult">
    <svg class="abs" style="left:0;top:0" width="187" height="231" viewBox="0 0 187 231">
      <path d="M0 0H187V215L93.5 231 0 215Z" fill="#2b2b2b"/>
      <path d="M0 0H187V37L93.5 51 0 37Z" fill="#b8975a"/>
    </svg>
    <div class="abs consult-copy">
      <p>CONTACT US NOW &amp; GET YOUR</p>
      <h3>FREE CONSULTATION</h3>
      <em>WELLNESS BEGINS HERE</em>
    </div>
    <div class="abs field" style="top:75px">First Name</div>
    <div class="abs field gold" style="top:96px">Last Name</div>
    <div class="abs field" style="top:118px">Phone Number</div>
    <div class="abs field" style="top:139px;height:40px">Comments ...</div>
    <div class="abs submit">Submit &#10140;</div>
  </div>

  <div class="abs badge-btn" style="top:653px"><span class="ico">P</span><span class="lbl">RATE US ON<b>PLEXO</b></span></div>
  <div class="abs badge-btn" style="top:688px"><span class="ico">C</span><span class="lbl">FIND US ON<b>CHATTERLY</b></span></div>

  <div class="abs hours">
    <h3>OFFICE HOURS</h3>
    <div>
      <div class="hours-row"><span>Monday</span><span>8:00-11:00 AM, 2:00-5:00 PM</span></div>
      <div class="hours-row"><span>Tuesday</span><span>8:30-11:00 AM, 2:00-5:30 PM</span></div>
      <div class="hours-row"><span>Wednesday</span><span>8:00-11:00 AM, 2:00-5:00 PM</span></div>
      <div class="hours-row"><span>Thursday</span><span>10:00-12:00 AM, 2:30-5:00 PM</span></div>
      <div class="hours-row"><span>Friday</span><span>8:00-10:00 AM, 1:00-5:00 PM</span></div>
      <div class="hours-row closed"><span>Saturday</span><span>Closed</span></div>
      <div class="hours-row closed"><span>Sunday</span><span>Closed</span></div>
    </div>
  </div>

  <h2 class="abs section-title" style="left:510px;top:910px;width:187px">Patient Testimonials</h2>
  <div class="abs quote">
    <span class="abs quote-mark">&ldquo;</span>
    <p class="abs quote-text">Pellentesque habitant morbi tristique senectus et netus et malesuada fames ac turpis egestas. Donec faucibus aliquet dui, nec congue orci sagittis eget. nteger leo justo, dapibus id mauris quis, vestibulum rutrum arcu. Etiam sed ipsum eu augue condimentum ullam corper vel ac sapien.</p>
    <div class="abs quote-foot"><span>- Mr. Daniel Rowe -</span><span class="dots"><span></span><span class="on"></span><span></span><span></span></span></div>
  </div>
</aside>

<footer>
  <div class="abs foot-links">
    <div class="abs foot-nav">Home<span>|</span>Why Fair Ridge?<span>|</span>How Chiropractic Helps<span>|</span>Ask the Doctor<span>|</span>Work Place Wellness<span>|</span>Request an Appointment<span>|</span>Blog<span>|</span>Contact Us</div>
    <div class="abs foot-brand"><i></i><div>FAIR RIDGE<small>CHIROPRACTIC</small></div></div>
  </div>
  <div class="abs foot-base">
    <div class="abs" style="left:108px;top:17px"><b>4172 North Maple Blvd, Suite #7</b><br><i style="padding-left:24px">Brookhaven, OR 97520</i></div>
    <div class="abs social" style="left:367px;top:15px;gap:6px"><span>C</span><span class="on">P</span><span>V</span></div>
    <div class="abs" style="left:562px;top:17px;text-align:right;width:135px"><b>Copyright &copy; 2015, Fair Ridge Chiropractic</b><br><i>Powered by <span style="color:var(--gold)">Crestline Pixel Group</span></i></div>
  </div>
</footer>

</body>
</html>
```